Business Cards - Brightpath Horizon

need to design unique business card for my mortgage business. I need to design credit card style business card for my business or any unique idea that you might have

Target Market(s)

Home Loan customers

Industry/Entity Type

Mortgage Brokerage

Contact Information for Business Card

please design credit card style or very unique style business card

Colors

Designer to choose colors to be used in the design.

Requirements
Must have
• Name
• position
• Phone number
• fax number
• email address
• website address
• social media address
• All above fields will be provided once design in finalised

```html
<!DOCTYPE html>
<html lang="en">
<head>
<meta charset="utf-8">
<title>Brightpath Horizon – Business Card</title>
<link href="https://fonts.googleapis.com/css2?family=Michroma&family=Noto+Serif:ital,wght@0,400;1,400&display=swap" rel="stylesheet">
<style>
  :root {
    --backdrop: #dcdcdc;
    --card: #1c1d1f;
    --card-edge: #242528;
    --brand-blue: #1f3fd8;
    --accent-orange: #e88a12;
    --text-light: #f2f2f2;
  }
  html, body {
    margin: 0;
    padding: 0;
    width: 1200px;
    height: 901px;
    overflow: hidden;
    background: var(--backdrop);
  }
  .canvas {
    position: relative;
    width: 1200px;
    height: 901px;
  }
  .card {
    position: absolute;
    left: 80px;
    top: 124px;
    width: 1040px;
    height: 653px;
    background: radial-gradient(ellipse at 50% 40%, var(--card-edge), var(--card) 75%);
    box-shadow: 0 14px 40px rgba(0,0,0,0.25);
    font-family: "Noto Serif", serif;
  }
  .brand {
    position: absolute;
    left: 0;
    right: 0;
    top: 170px;
    text-align: center;
    color: var(--brand-blue);
    font-weight: 400;
    line-height: 1;
  }
  .brand-line-small {
    display: block;
    font-size: 40px;
    letter-spacing: 2px;
  }
  .brand-line-large {
    display: block;
    font-size: 84px;
    margin-top: 4px;
  }
  .tagline {
    position: absolute;
    left: 0;
    right: 0;
    top: 300px;
    text-align: center;
    font-style: italic;
    color: var(--accent-orange);
    font-size: 28px;
  }
  .person {
    position: absolute;
    left: 55px;
    top: 435px;
  }
  .person-name {
    color: var(--brand-blue);
    font-size: 38px;
    line-height: 1;
    margin: 0;
  }
  .person-role {
    color: var(--accent-orange);
    font-size: 28px;
    margin: 14px 0 0;
    line-height: 1;
  }
  .social-list {
    position: absolute;
    left: 55px;
    top: 550px;
    display: flex;
    gap: 6px;
  }
  .social-dot {
    width: 45px;
    height: 45px;
    border-radius: 50%;
    background: var(--brand-blue);
  }
  .contact {
    position: absolute;
    right: 55px;
    top: 436px;
    text-align: right;
  }
  .contact-phone {
    font-family: "Michroma", sans-serif;
    color: var(--brand-blue);
    font-size: 30px;
    letter-spacing: 6px;
    line-height: 1;
    margin: 0 0 26px;
  }
  .contact-row {
    display: flex;
    justify-content: flex-end;
    align-items: center;
    gap: 12px;
    color: var(--text-light);
    font-size: 25px;
    line-height: 1;
    margin-bottom: 12px;
  }
  .contact-icon {
    width: 24px;
    height: 24px;
    flex: none;
  }
</style>
</head>
<body>
<div class="canvas">
  <div class="card">
    <div class="brand">
      <span class="brand-line-small">BRIGHTPATH</span>
      <span class="brand-line-large">HORIZON</span>
    </div>
    <div class="tagline">Sound advice,Every step</div>

    <div class="person">
      <p class="person-name">DANIEL REYES</p>
      <p class="person-role">CEO/FOUNDER</p>
    </div>

    <div class="social-list" aria-label="Social media profiles">
      <div class="social-dot"></div>
      <div class="social-dot"></div>
      <div class="social-dot"></div>
      <div class="social-dot"></div>
    </div>

    <div class="contact">
      <p class="contact-phone">415 270 3856</p>
      <div class="contact-row">
        <span>Fax: 415 270 3857</span>
        <svg class="contact-icon" viewBox="0 0 24 24" aria-hidden="true">
          <rect x="6" y="3" width="12" height="6" fill="var(--brand-blue)"/>
          <rect x="2" y="9" width="20" height="9" rx="2" fill="var(--brand-blue)"/>
          <rect x="6" y="14" width="12" height="7" fill="var(--card)" stroke="var(--brand-blue)" stroke-width="2"/>
        </svg>
      </div>
      <div class="contact-row">
        <span>hello@brightpathhq.com</span>
        <svg class="contact-icon" viewBox="0 0 24 24" aria-hidden="true">
          <rect x="2" y="5" width="20" height="14" rx="1" fill="var(--brand-blue)"/>
          <path d="M2 6 L12 13 L22 6" fill="none" stroke="var(--card)" stroke-width="2"/>
        </svg>
      </div>
      <div class="contact-row">
        <span>www.brightpathhq.com</span>
        <svg class="contact-icon" viewBox="0 0 24 24" aria-hidden="true">
          <circle cx="12" cy="12" r="10" fill="var(--brand-blue)"/>
          <ellipse cx="12" cy="12" rx="4" ry="10" fill="none" stroke="var(--card)" stroke-width="1.6"/>
          <line x1="2" y1="12" x2="22" y2="12" stroke="var(--card)" stroke-width="1.6"/>
        </svg>
      </div>
    </div>
  </div>
</div>
</body>
</html>
```